Counseling Practice Business Card

I need a professional looking business card incorporating my new logo that was just completed. Card needs to incorporate my name and title, description of my specialty, my address, my phone number, my fax number, my email and my website URL. I need to be able to choose design on/with different paper colors and textures.
I do not have a lot of business card ideas so I am open to anything but I want bold,sharp, clear card without additional designs other than my logo (see attached file info). I am open to different color backgrounds or paper colors including black. I do not like traditional brackets around area codes in phone number or dashes between numbers in phone number. Am open to other ways of presenting including periods between numbers as appropriate. I do not know enough to know what I like yet but I want card to coordinate and work together with my logo. My practice emphasizes natural mental health interventions so any use of color (with background paper color or the blue and green in my logo) that elicits nature is nice. In addition to black, any natural brown or wood looking background might be desirable also. Most of the offerings so far look very similar and boring.

Target Market(s)

Potential therapy clients and other professionals

Contact Information for Business Card

Card information:
Gerald M. Whitcombe, Ph.D.
Licensed Clinical Psychologist
Integrative Health Coach
4812 Marlowe Ridge Blvd SE
Suite 310
Duluth, GA 30096
(770) 415-2983 phone
(770) 581-4096 fax
drgeraldwhitcombe@quillmarsh.net
brightfernwellness.net

Font styles to use
Serif
Sans Serif
Other font styles liked:
• anything that you think looks crisp, clear and easily readable

Requirements
Must have
• Any color used should coordinate with my logo design (see attached files).
• Card should be printed horizontally so top and bottom are longest sides of rectangle.
• Background color or paper color should complement and highlight logo. Do not like a white background. black, grey, brown or any color my logo would blend well with.
Nice to have
• I would like designer to utilize color to highlight letters/name or phone-fax-web symbols.
• Bottom edge of card could be highlighted if appropriate to an idea.
Should not have
• I would NOT want the card to have a pure white background at all.
• No clear cards.
• Cards should be oriented with long sides on bottom and top, NOT sides. DO NOT LIKE THIS THIN TALL ORIENTATION.

```html
<!DOCTYPE html>
<html lang="en">
<head>
<meta charset="utf-8">
<title>Brightfern Wellness – Business Card</title>
<link href="https://fonts.googleapis.com/css2?family=Source+Sans+3:wght@400;600&family=Roboto+Condensed:wght@700&display=swap" rel="stylesheet">
<style>
  :root {
    --backdrop: #2b2b2b;
    --card: #151515;
    --brand-blue: #2a76bd;
    --brand-green: #0b6a35;
    --text-light: #d2d2d2;
    --white: #ffffff;
    --silver: #d9d9d9;
    --icon-blue: #2f7fc8;
  }
  * { margin: 0; padding: 0; box-sizing: border-box; }
  html, body { width: 1200px; height: 960px; overflow: hidden; }
  body {
    background: var(--backdrop);
    position: relative;
    font-family: "Source Sans 3", sans-serif;
  }
  .card {
    position: absolute;
    left: 302px;
    width: 598px;
    height: 342px;
    background: var(--card);
    box-shadow: 0 4px 14px rgba(0,0,0,.55);
    overflow: hidden;
  }
  .card--front { top: 123px; }
  .card--back { top: 497px; display: flex; align-items: center; justify-content: center; }

  .front__swoosh { position: absolute; inset: 0; width: 598px; height: 342px; }

  .brand-name {
    position: absolute;
    left: 30px;
    top: 40px;
    font-size: 34px;
    font-weight: 600;
    color: var(--brand-blue);
    letter-spacing: .2px;
  }
  .address {
    position: absolute;
    left: 48px;
    top: 126px;
    font-size: 15px;
    line-height: 20px;
    color: var(--text-light);
  }
  .contact-list {
    position: absolute;
    left: 48px;
    top: 175px;
    list-style: none;
    font-size: 15px;
    color: var(--text-light);
  }
  .contact-list li { display: flex; align-items: center; height: 19px; }
  .contact-list svg { width: 13px; height: 13px; margin-right: 10px; fill: var(--icon-blue); }

  .person {
    position: absolute;
    right: 18px;
    top: 260px;
    text-align: right;
    color: var(--white);
  }
  .person__name {
    font-family: "Roboto Condensed", sans-serif;
    font-weight: 700;
    font-size: 19px;
    text-transform: uppercase;
    letter-spacing: .2px;
    line-height: 24px;
  }
  .person__title { font-size: 15.5px; line-height: 21px; }

  .back__brand {
    font-size: 58px;
    font-weight: 600;
    color: var(--silver);
    letter-spacing: .5px;
  }
</style>
</head>
<body>

<section class="card card--front">
  <svg class="front__swoosh" viewBox="0 0 598 342" aria-hidden="true">
    <path d="M168,342 C380,262 538,150 546,0 L566,0 C576,150 420,270 228,342Z" fill="var(--brand-green)"/>
    <path d="M222,342 C418,270 572,150 562,0 L598,0 L598,342Z" fill="#0a0a0a"/>
    <path d="M228,342 C424,270 578,150 568,0 L598,0 L598,342Z" fill="var(--brand-blue)"/>
  </svg>

  <div class="brand-name">Brightfern Wellness</div>

  <p class="address">4812 Marlowe Ridge Blvd SE<br>Suite 310, Duluth, GA 30096</p>

  <ul class="contact-list">
    <li><svg viewBox="0 0 16 16"><path d="M1 5c0-2 3-3 7-3s7 1 7 3v1.5h-3.5V5H4.5v1.5H1z M3 8l2-2h6l2 2v6H3z M8 8.5a2 2 0 1 0 0 4a2 2 0 1 0 0-4z"/></svg>(770) 415-2983</li>
    <li><svg viewBox="0 0 16 16"><path d="M4 1h8v4H4z M1 6h14v7h-3v2H4v-2H1z M5 10v4h6v-4z"/></svg>(770) 581-4096</li>
    <li><svg viewBox="0 0 16 16"><path d="M1 3h14v1.5L8 9 1 4.5z M1 6.5l7 4.5 7-4.5V13H1z"/></svg>drgeraldwhitcombe@quillmarsh.net</li>
    <li><svg viewBox="0 0 16 16"><path d="M8 1a7 7 0 1 0 0 14A7 7 0 1 0 8 1z M5 4c2 0 3 1 2 2s-2 1-2 3-2 1-2-1c0-2 1-4 2-4z M10 8c2 0 2 2 1 3s-2 2-3 1 0-4 2-4z" fill-rule="evenodd"/></svg>www.brightfernwellness.net</li>
  </ul>

  <div class="person">
    <div class="person__name">Gerald M. Whitcombe, Ph.D.</div>
    <div class="person__title">Licensed Clinical Psychologist</div>
    <div class="person__title">Integrative Health Coach</div>
  </div>
</section>

<section class="card card--back">
  <div class="back__brand">Brightfern Wellness</div>
</section>

</body>
</html>
```